Mortgage Protection Insurance Flyer

The target audience are new home owners so the design needs to be clean and simple.

This a primarily for Final Expense Insurance, but need an area where it says "We Also Specialize In:"
- Medicare Supplement Insurance (MediGap)
- Annuities
- Final Expense

All flyer versions need to be editable. Colors to be used are red, white or black. Refer to my website for colors and photos (corvantshield.com). Will attach my logo and a flyer that I found online that is the format that I am looking for (for 8.5 in. x 11 in version). Need flyer in standard letter size 8.5 in. x11 in. but also in 8.5 in. x 5.5 in and 5.0 in. x 8.0 in. All sizes to be portrait oriented. If picked as winning design, need all flyer versions in full color, also in grey scale and files in all industry file types.

Content can be taken from my website..... corvantshield.com

Do NOT submit if you are not willing to provide all versions as described above for the original project price.

Must use royalty-free stock photos please.

Target Market(s)

New homeowners looking for insurance to protect there mortgage payments

Industry/Entity Type

Life Insurance

Colors
f69fa3

Requirements
Must have
• Colors to be used are red, white or black.
• Need flyer in standard letter size 8.5 in. x11 in. but also in 3.5 in. x 8.5 in (Full Bleed 3.75 in by 8.75 in.) and 4.0 in. x 6.0 in. (Full Bleed 4.12 in x 6.12 in) Each design tailored to the size dimensions (So no squeezing 8.5 x 11 design into a 4.0 x 6.0 space.) All sizes to be portrait oriented. If picked as winning design, need all flyer versions in full color, also in grey scale and files in all file types.
• Do not need physical address on flyer, do need email address on flyer though - tkelwer@corvantshield.com
• So phone number should be prominent, email address and website address should also be contact area.
• If you can not agree to terms above, do not submit any designs.
• Need facebook & twitter logos somewhere in contact info area.
Nice to have
• See sample flyers I have attached.
• White background with red used as primary graphic color and black used as secondary graphic if needed.
• font to be used should similar to one used in logo.

```html
<!DOCTYPE html>
<html lang="en">
<head>
<meta charset="utf-8">
<title>Corvant Shield – Final Expense Flyer Set</title>
<link href="https://fonts.googleapis.com/css2?family=Lato:wght@400;700;900&family=Oswald:wght@500;700&display=swap" rel="stylesheet">
<style>
  :root{
    --red:#e3151c;
    --red-deep:#b30c11;
    --ink:#1d1d1d;
    --ink-soft:#3a3a3a;
    --paper:#ffffff;
    --bar-grey:#cdcdcd;
    --text-grey:#444444;
    --label-grey:#6b6b6b;
    --pink:#ffaaaa;
    --pink-soft:#ffcaca;
    --slate:#b4b4b4;
    --slate-soft:#d3d3d3;
    --slate-mid:#bdbdbd;
    --photo-light:#f4ede6;
    --photo-mid:#e2d3c4;
    --photo-dark:#c9b19b;
  }
  *{box-sizing:border-box;margin:0;padding:0}
  html,body{width:1040px;height:1200px;overflow:hidden}
  body{position:relative;font-family:"Lato",sans-serif;color:var(--ink);background:var(--slate)}
  .defs{position:absolute;width:0;height:0;overflow:hidden}

  /* presentation board */
  .zone{position:absolute}
  .zone-a{left:0;top:0;width:450px;height:586px;background:var(--pink)}
  .zone-b{left:450px;top:0;width:252px;height:586px;background:var(--pink-soft)}
  .zone-c{left:702px;top:0;width:338px;height:586px;background:var(--pink)}
  .zone-d{left:0;top:586px;width:450px;height:614px;background:var(--slate)}
  .zone-e{left:450px;top:586px;width:252px;height:614px;background:var(--slate-soft)}
  .zone-f{left:702px;top:586px;width:338px;height:614px;background:var(--slate-mid)}
  .size-label{position:absolute;width:200px;margin-left:-100px;text-align:center;font-weight:900;font-size:22px;color:var(--label-grey);letter-spacing:.5px}

  /* flyer frame */
  .flyer{position:absolute;overflow:hidden;background:var(--paper);box-shadow:0 1px 3px rgba(0,0,0,.15)}
  .flyer.mono{filter:grayscale(1)}
  .sheet{position:absolute;left:0;top:0;transform:scale(.8);transform-origin:0 0;background:var(--paper)}
  .letter{width:365px;height:470px}
  .letter .sheet{width:456px;height:587px}
  .rack{width:202px;height:470px}
  .rack .sheet{width:252px;height:587px}
  .postcard{width:252px;height:374px}
  .postcard .sheet{width:315px;height:467px}
  .art{position:absolute;left:0;top:0;width:100%;height:100%}
  .sheet > *:not(.art){position:absolute}

  .fill-photo{fill:url(#photo-tone)}
  .fill-footer{fill:url(#footer-red)}
  .fill-paper{fill:var(--paper)}
  .line-ink{fill:none;stroke:var(--ink)}
  .line-red{fill:none;stroke:var(--red)}
  .line-grey{fill:none;stroke:#8d8d8d}
  .stop-red{stop-color:var(--red)}
  .stop-deep{stop-color:var(--red-deep)}
  .stop-photo-light{stop-color:var(--photo-light)}
  .stop-photo-mid{stop-color:var(--photo-mid)}
  .stop-photo-dark{stop-color:var(--photo-dark)}
  .stop-paper{stop-color:#ffffff}

  /* brand */
  .brand{display:flex;align-items:center;gap:4px}
  .brand-mark{display:block;background:var(--red)}
  .brand-name{font-weight:900;color:var(--ink);letter-spacing:.3px;white-space:nowrap}

  /* headline */
  .headline{font-family:"Oswald",sans-serif;font-weight:700;line-height:1;text-transform:uppercase}
  .headline span{display:block}
  .headline .accent{color:var(--red)}

  /* benefits */
  .benefits{background:linear-gradient(160deg,var(--red),var(--red-deep));color:#fff}
  .benefits-tab{position:absolute;left:-6px;background:var(--ink-soft);color:#fff;font-weight:900;border-radius:0 6px 6px 0}
  .benefit-list{list-style:none}
  .benefit-list li{display:flex;align-items:flex-start;font-weight:700;line-height:1.25}
  .tick{flex:none;color:#fff}

  .section-title{color:var(--red);font-weight:900}
  .body-copy p{color:var(--text-grey);line-height:1.3}
  .justify p{text-align:justify}

  .rates{display:flex;flex-direction:column}
  .rate{display:flex}
  .rate dt{background:var(--bar-grey);color:var(--ink);font-weight:700}
  .rate dd{background:var(--red);color:#fff;font-weight:900;text-align:center}

  .also-title{color:var(--red);font-weight:900}
  .also-list{list-style:none;color:var(--text-grey)}
  .also-list li{display:flex;align-items:center}
  .also-list .tick{color:var(--red)}
  .footnote{color:var(--text-grey);line-height:1.3}

  .call{color:#fff;line-height:1}
  .call-label{display:block;font-weight:700}
  .call-number{display:block;font-weight:900}
  .contact-line{display:flex;align-items:center;color:#fff;font-weight:700;white-space:nowrap}
  .contact-icon{flex:none;color:#fff}
  .social{display:flex;gap:2px}
  .social span{display:block;background:#fff}

  /* ---- letter 8.5x11 ---- */
  .letter .brand{left:22px;top:28px}
  .letter .brand-mark{width:8px;height:8px}
  .letter .brand-name{font-size:16px}
  .letter .headline{left:22px;top:118px}
  .letter .headline span:nth-child(1){font-size:36px}
  .letter .headline span:nth-child(2){font-size:32px;margin-top:1px}
  .letter .headline span:nth-child(3){font-size:20px;margin-top:3px}
  .letter .benefits{left:258px;top:197px;width:180px;height:188px;border-radius:10px;padding:40px 10px 0 12px}
  .letter .benefits-tab{top:14px;font-size:12px;padding:3px 14px 3px 12px}
  .letter .benefit-list li{font-size:6.3px;margin-bottom:9px}
  .letter .benefit-list .tick{width:8px;height:8px;margin-right:6px;margin-top:-1px}
  .letter .section-title{left:22px;top:268px;font-size:9px}
  .letter .intro{left:22px;top:285px;width:213px}
  .letter .body-copy p{font-size:5.7px;margin-bottom:7px}
  .letter .rates{left:22px;top:334px;gap:4px}
  .letter .rate dt{width:143px;font-size:5.5px;padding:1.5px 4px}
  .letter .rate dd{width:66px;margin-left:2px;font-size:6px;padding:1.5px 0}
  .letter .story{left:22px;top:375px;width:225px}
  .letter .also-title{left:270px;top:418px;font-size:9px}
  .letter .also-list{left:270px;top:436px}
  .letter .also-list li{font-size:6.6px;margin-bottom:5px}
  .letter .also-list .tick{width:7px;height:7px;margin-right:5px}
  .letter .footnote{left:270px;top:486px;font-size:4.6px}
  .letter .call{left:22px;top:525px}
  .letter .call-label{font-size:13px}
  .letter .call-number{font-size:21px;margin-top:3px}
  .letter .contact-email{left:203px;top:543px;font-size:5.3px}
  .letter .contact-web{left:340px;top:543px;font-size:5.3px}
  .letter .contact-icon{width:13px;height:13px;margin-right:5px}
  .letter .social{left:418px;top:562px}
  .letter .social span{width:5px;height:5px}

  /* ---- rack 3.5x8.5 ---- */
  .rack .brand{left:18px;top:24px}
  .rack .brand-mark{width:6px;height:6px}
  .rack .brand-name{font-size:11.5px}
  .rack .headline{left:18px;top:92px}
  .rack .headline span:nth-child(1){font-size:25px}
  .rack .headline span:nth-child(2){font-size:20px;margin-top:1px}
  .rack .headline span:nth-child(3){font-size:13px;margin-top:2px}
  .rack .benefits{left:120px;top:150px;width:115px;height:152px;border-radius:7px;padding:22px 6px 0 7px}
  .rack .benefits-tab{top:8px;font-size:6px;padding:2px 8px 2px 8px}
  .rack .benefit-list li{font-size:4.6px;margin-bottom:6px}
  .rack .benefit-list .tick{width:6px;height:6px;margin-right:4px}
  .rack .section-title{left:20px;top:220px;width:90px;font-size:7px;line-height:1.1}
  .rack .intro{left:20px;top:245px;width:92px}
  .rack .body-copy p{font-size:4.3px;margin-bottom:6px}
  .rack .rates{left:20px;top:314px;gap:3px}
  .rack .rate dt{width:110px;font-size:4px;padding:1px 3px}
  .rack .rate dd{width:56px;margin-left:2px;font-size:4.4px;padding:1px 0}
  .rack .story{left:20px;top:346px;width:208px}
  .rack .also-title{left:20px;top:456px;font-size:6.5px}
  .rack .also-list{left:20px;top:470px;width:200px;display:grid;grid-template-columns:140px 60px;row-gap:3px}
  .rack .also-list li{font-size:4.3px}
  .rack .also-list .tick{width:5px;height:5px;margin-right:3px}
  .rack .footnote{left:98px;top:498px;font-size:3.6px;text-align:center}
  .rack .call{left:17px;top:538px}
  .rack .call-label{font-size:8.5px}
  .rack .call-number{font-size:12.5px;margin-top:2px}
  .rack .contact-email{left:117px;top:537px;font-size:3.8px}
  .rack .contact-web{left:117px;top:553px;font-size:3.8px}
  .rack .contact-icon{width:10px;height:10px;margin-right:4px}
  .rack .social{left:198px;top:567px}
  .rack .social span{width:4px;height:4px}

  /* ---- postcard 4x6 ---- */
  .postcard .brand{left:22px;top:30px}
  .postcard .brand-mark{width:6px;height:6px}
  .postcard .brand-name{font-size:12.5px}
  .postcard .headline{left:22px;top:98px}
  .postcard .headline span:nth-child(1){font-size:25px}
  .postcard .headline span:nth-child(2){font-size:21px;margin-top:1px}
  .postcard .headline span:nth-child(3){font-size:13px;margin-top:2px}
  .postcard .benefits{left:170px;top:103px;width:131px;height:165px;border-radius:8px;padding:25px 7px 0 8px}
  .postcard .benefits-tab{top:9px;font-size:6.5px;padding:2px 9px 2px 9px}
  .postcard .benefit-list li{font-size:5px;margin-bottom:6.5px}
  .postcard .benefit-list .tick{width:6px;height:6px;margin-right:4px}
  .postcard .section-title{left:22px;top:196px;font-size:6.5px}
  .postcard .intro{left:22px;top:209px;width:135px}
  .postcard .body-copy p{font-size:4.3px;margin-bottom:6px}
  .postcard .rates{left:22px;top:253px;gap:3px}
  .postcard .rate dt{width:90px;font-size:4.2px;padding:1px 3px}
  .postcard .rate dd{width:40px;margin-left:2px;font-size:4.4px;padding:1px 0}
  .postcard .story{left:22px;top:281px;width:272px}
  .postcard .also-title{left:22px;top:357px;font-size:6px}
  .postcard .also-list{left:22px;top:370px;display:flex;gap:14px}
  .postcard .also-list li{font-size:4.2px}
  .postcard .also-list .tick{width:5px;height:5px;margin-right:3px}
  .postcard .footnote{left:155px;top:388px;font-size:3.6px;text-align:center}
  .postcard .call{left:29px;top:421px}
  .postcard .call-label{font-size:8.5px}
  .postcard .call-number{font-size:13px;margin-top:2px}
  .postcard .contact-email{left:152px;top:420px;font-size:4.2px}
  .postcard .contact-web{left:152px;top:438px;font-size:4.2px}
  .postcard .contact-icon{width:11px;height:11px;margin-right:5px}
  .postcard .social{left:267px;top:451px}
  .postcard .social span{width:4px;height:4px}
</style>
</head>
<body>

<svg class="defs" aria-hidden="true">
  <defs>
    <linearGradient id="photo-tone" x1="0" y1="0" x2="1" y2="0.3">
      <stop offset="0" class="stop-paper"/>
      <stop offset="0.35" class="stop-photo-light"/>
      <stop offset="0.7" class="stop-photo-mid"/>
      <stop offset="1" class="stop-photo-dark"/>
    </linearGradient>
    <linearGradient id="footer-red" x1="0" y1="0" x2="0" y2="1">
      <stop offset="0" class="stop-red"/>
      <stop offset="1" class="stop-deep"/>
    </linearGradient>
    <symbol id="tick" viewBox="0 0 10 10">
      <circle cx="5" cy="5" r="4.3" fill="none" stroke="currentColor" stroke-width="1"/>
      <path d="M2.9 5.1 4.4 6.6 7.2 3.6" fill="none" stroke="currentColor" stroke-width="1.2"/>
    </symbol>
    <symbol id="mail" viewBox="0 0 14 14">
      <circle cx="7" cy="7" r="6.3" fill="none" stroke="currentColor" stroke-width="1"/>
      <rect x="3.8" y="4.8" width="6.4" height="4.4" fill="none" stroke="currentColor" stroke-width=".9"/>
      <path d="M3.8 4.8 7 7.4 10.2 4.8" fill="none" stroke="currentColor" stroke-width=".9"/>
    </symbol>
    <symbol id="globe" viewBox="0 0 14 14">
      <circle cx="7" cy="7" r="6.3" fill="none" stroke="currentColor" stroke-width="1"/>
      <circle cx="7" cy="7" r="3.4" fill="none" stroke="currentColor" stroke-width=".9"/>
      <ellipse cx="7" cy="7" rx="1.5" ry="3.4" fill="none" stroke="currentColor" stroke-width=".8"/>
      <path d="M3.6 7H10.4" stroke="currentColor" stroke-width=".8"/>
    </symbol>
  </defs>
</svg>

<div class="zone zone-a"></div><div class="zone zone-b"></div><div class="zone zone-c"></div>
<div class="zone zone-d"></div><div class="zone zone-e"></div><div class="zone zone-f"></div>

<!-- ================= Letter, colour ================= -->
<article class="flyer letter" style="left:42px;top:44px">
  <div class="sheet">
    <svg class="art" viewBox="0 0 456 587">
      <path role="img" aria-label="Photo of a smiling senior couple embracing at home" class="fill-photo" d="M150,0H456V214C300,200 150,236 0,230V112C70,104 132,62 150,0Z"/>
      <path class="fill-paper" d="M0,0H176C156,64 90,112 0,120Z"/>
      <path class="line-ink" stroke-width="3" d="M0,121C86,112 154,64 176,0"/>
      <path class="line-red" stroke-width="1.5" d="M0,128C94,118 166,66 188,0"/>
      <path class="fill-paper" d="M0,230C150,236 300,204 456,208V260H0Z"/>
      <path class="line-ink" stroke-width="5" d="M0,229C150,237 300,205 456,208"/>
      <path class="line-grey" stroke-width="1.5" d="M0,238C150,244 300,214 456,217"/>
      <path class="line-ink" stroke-width="4" d="M0,523C150,492 300,514 456,496"/>
      <path class="fill-footer" d="M0,530C150,500 300,520 456,503V587H0Z"/>
    </svg>
    <div class="brand"><span class="brand-mark"></span><span class="brand-name">CORVANT SHIELD</span></div>
    <h1 class="headline"><span>Our</span><span class="accent">Plans Are</span><span>Based on Yours</span></h1>
    <section class="benefits">
      <h2 class="benefits-tab">Benefits:</h2>
      <ul class="benefit-list">
        <li><svg class="tick"><use href="#tick"/></svg>All plans we offer are state regulated</li>
        <li><svg class="tick"><use href="#tick"/></svg>Relatively low monthly premiums</li>
        <li><svg class="tick"><use href="#tick"/></svg>Premiums can never increase</li>
        <li><svg class="tick"><use href="#tick"/></svg>Your policy can never be cancelled as long as you pay your premium</li>
        <li><svg class="tick"><use href="#tick"/></svg>No medical exams</li>
        <li><svg class="tick"><use href="#tick"/></svg>Guaranteed Death Benefit</li>
        <li><svg class="tick"><use href="#tick"/></svg>Many policies we offer are Guaranteed Acceptance, "Day 1" coverage, have a child/grandchild rider and/or have an accelerated death benefit rider</li>
      </ul>
    </section>
    <h2 class="section-title">Final Expense Insurance</h2>
    <div class="body-copy justify intro"><p>Final Expense Insurance is a type of permanent whole life insurance insurance where the death benefit is used to cover (but not limited to) medical costs, funeral costs and other end-of-life expenses. It is a budget friendly option with a death benefit of up to $40k.</p></div>
    <dl class="rates">
      <div class="rate"><dt>Monthly premiums as low as</dt><dd>$11*</dd></div>
      <div class="rate"><dt>Death Benefits as high as</dt><dd>$40,000</dd></div>
    </dl>
    <div class="body-copy story">
      <p>Unforeseen events and a lack of the right kind of insurance can spell trouble quickly. Contact us today, to set up a free assessment time. We will analyze your insurance needs and get you and your family the right coverage quickly at a budget friendly price.</p>
      <p>We have been helping clients in Northern Idaho/Eastern Washington prepare for the unknown.</p>
      <p>We have access to the industry's top insurance carriers so you can get the right coverage, that fits your budget.</p>
      <p>Find out how we can give you the peace of mind of knowing your family will not have a financial burden if something were to happen to you.</p>
    </div>
    <h2 class="also-title">We Also Specialize In:</h2>
    <ul class="also-list">
      <li><svg class="tick"><use href="#tick"/></svg>Medicare Supplement Insurance (Medigap)</li>
      <li><svg class="tick"><use href="#tick"/></svg>Annuities</li>
      <li><svg class="tick"><use href="#tick"/></svg>Mortgage Protection Insurance</li>
    </ul>
    <p class="footnote">*Based on an insured that is a 65 year old, non-smoking female<br>that has no medical conditions with a death benefit of $2k</p>
    <p class="call"><span class="call-label">Call us now:</span><span class="call-number">(208)555.0147</span></p>
    <p class="contact-line contact-email"><svg class="contact-icon"><use href="#mail"/></svg>tkelwer@corvantshield.com</p>
    <p class="contact-line contact-web"><svg class="contact-icon"><use href="#globe"/></svg>corvantshield.com</p>
    <div class="social"><span></span><span></span></div>
  </div>
</article>

<!-- ================= Rack, colour ================= -->
<article class="flyer rack" style="left:476px;top:47px">
  <div class="sheet">
    <svg class="art" viewBox="0 0 252 587">
      <path role="img" aria-label="Photo of a smiling senior couple embracing at home" class="fill-photo" d="M105,0H252V180C170,174 80,196 0,192V68C55,62 95,36 105,0Z"/>
      <path class="line-ink" stroke-width="2.5" d="M0,70C56,63 96,36 108,0"/>
      <path class="line-red" stroke-width="1.2" d="M0,75C62,68 104,38 116,0"/>
      <path class="fill-paper" d="M0,192C80,198 170,176 252,180V215H0Z"/>
      <path class="line-ink" stroke-width="4" d="M0,191C80,198 170,175 252,179"/>
      <path class="line-grey" stroke-width="1.2" d="M0,198C80,205 170,183 252,187"/>
      <path class="line-ink" stroke-width="3.5" d="M0,527C80,505 170,522 252,506"/>
      <path class="fill-footer" d="M0,533C80,511 170,528 252,512V587H0Z"/>
    </svg>
    <div class="brand"><span class="brand-mark"></span><span class="brand-name">CORVANT SHIELD</span></div>
    <h1 class="headline"><span>Our</span><span class="accent">Plans Are</span><span>Based on Yours</span></h1>
    <section class="benefits">
      <h2 class="benefits-tab">Benefits:</h2>
      <ul class="benefit-list">
        <li><svg class="tick"><use href="#tick"/></svg>All plans we offer are state regulated</li>
        <li><svg class="tick"><use href="#tick"/></svg>Relatively low monthly premiums</li>
        <li><svg class="tick"><use href="#tick"/></svg>Premiums can never increase</li>
        <li><svg class="tick"><use href="#tick"/></svg>Your policy can never be cancelled as long as you pay your premium</li>
        <li><svg class="tick"><use href="#tick"/></svg>No medical exams</li>
        <li><svg class="tick"><use href="#tick"/></svg>Guaranteed Death Benefit</li>
        <li><svg class="tick"><use href="#tick"/></svg>Many policies we offer are Guaranteed Acceptance, "Day 1" coverage, have a child/grandchild rider and/or have an accelerated death benefit rider</li>
      </ul>
    </section>
    <h2 class="section-title">Final Expense Insurance</h2>
    <div class="body-copy justify intro"><p>Final Expense Insurance is a type of permanent whole life insurance where the death benefit is used to cover (but not limited to) medical costs, funeral costs and other end-of-life expenses. It is a budget friendly option with a death benefit of up to $40k.</p></div>
    <dl class="rates">
      <div class="rate"><dt>Monthly premiums as low as</dt><dd>$11*</dd></div>
      <div class="rate"><dt>Death Benefits as high as</dt><dd>$40,000</dd></div>
    </dl>
    <div class="body-copy story">
      <p>Unforeseen events and a lack of the right kind of insurance can spell trouble quickly. Contact us today, to set up a free assessment time. We will analyze your insurance needs and get you and your family the right coverage quickly at a budget friendly price.</p>
      <p>We have been helping clients in Northern Idaho/Eastern Washington prepare for the unknown.</p>
      <p>We have access to the industry's top insurance carriers so you can get the right coverage, that fits your budget.</p>
      <p>Find out how we can give you the peace of mind of knowing your family will not have a financial burden if something were to happen to you.</p>
    </div>
    <h2 class="also-title">We Also Specialize In:</h2>
    <ul class="also-list">
      <li><svg class="tick"><use href="#tick"/></svg>Medicare Supplement Insurance (Medigap)</li>
      <li><svg class="tick"><use href="#tick"/></svg>Annuities</li>
      <li><svg class="tick"><use href="#tick"/></svg>Mortgage Protection Insurance</li>
    </ul>
    <p class="footnote">*Based on an insured that is a 65 year old, non-smoking female<br>that has no medical conditions with a death benefit of $2k</p>
    <p class="call"><span class="call-label">Call us now:</span><span class="call-number">(208)555.0147</span></p>
    <p class="contact-line contact-email"><svg class="contact-icon"><use href="#mail"/></svg>tkelwer@corvantshield.com</p>
    <p class="contact-line contact-web"><svg class="contact-icon"><use href="#globe"/></svg>corvantshield.com</p>
    <div class="social"><span></span><span></span></div>
  </div>
</article>

<!-- ================= Postcard, colour ================= -->
<article class="flyer postcard" style="left:746px;top:143px">
  <div class="sheet">
    <svg class="art" viewBox="0 0 315 467">
      <path role="img" aria-label="Photo of a smiling senior couple embracing at home" class="fill-photo" d="M128,0H315V176C220,168 100,192 0,188V74C62,68 114,42 128,0Z"/>
      <path class="line-ink" stroke-width="2.5" d="M0,76C64,69 116,42 130,0"/>
      <path class="line-red" stroke-width="1.2" d="M0,81C70,74 124,44 138,0"/>
      <path class="fill-paper" d="M0,188C100,194 220,172 315,176V205H0Z"/>
      <path class="line-ink" stroke-width="4" d="M0,187C100,195 220,171 315,175"/>
      <path class="line-grey" stroke-width="1.2" d="M0,194C100,202 220,179 315,183"/>
      <path class="line-ink" stroke-width="3.5" d="M0,412C100,390 220,406 315,392"/>
      <path class="fill-footer" d="M0,418C100,396 220,412 315,398V467H0Z"/>
    </svg>
    <div class="brand"><span class="brand-mark"></span><span class="brand-name">CORVANT SHIELD</span></div>
    <h1 class="headline"><span>Our</span><span class="accent">Plans Are</span><span>Based on Yours</span></h1>
    <section class="benefits">
      <h2 class="benefits-tab">Benefits:</h2>
      <ul class="benefit-list">
        <li><svg class="tick"><use href="#tick"/></svg>All plans we offer are state regulated</li>
        <li><svg class="tick"><use href="#tick"/></svg>Relatively low monthly premiums</li>
        <li><svg class="tick"><use href="#tick"/></svg>Premiums can never increase</li>
        <li><svg class="tick"><use href="#tick"/></svg>Your policy can never be cancelled as long as you pay your premium</li>
        <li><svg class="tick"><use href="#tick"/></svg>No medical exams</li>
        <li><svg class="tick"><use href="#tick"/></svg>Guaranteed Death Benefit</li>
        <li><svg class="tick"><use href="#tick"/></svg>Many policies we offer are Guaranteed Acceptance, "Day 1" coverage, have a child/grandchild rider and/or have an accelerated death benefit rider</li>
      </ul>
    </section>
    <h2 class="section-title">Final Expense Insurance</h2>
    <div class="body-copy justify intro"><p>Final Expense Insurance is a type of permanent whole life insurance where the death benefit is used to cover (but not limited to) medical costs, funeral costs and other end-of-life expenses. It is a budget friendly option with a death benefit of up to $40k.</p></div>
    <dl class="rates">
      <div class="rate"><dt>Monthly premiums as low as</dt><dd>$11*</dd></div>
      <div class="rate"><dt>Death Benefits as high as</dt><dd>$40,000</dd></div>
    </dl>
    <div class="body-copy story">
      <p>Unforeseen events and a lack of the right kind of insurance can spell trouble quickly. Contact us today, to set up a free assessment time. We will analyze your insurance needs and get you and your family the right coverage quickly at a budget friendly price.</p>
      <p>We have been helping clients in Northern Idaho/Eastern Washington prepare for the unknown.</p>
      <p>We have access to the industry's top insurance carriers so you can get the right coverage, that fits your budget.</p>
      <p>Find out how we can give you the peace of mind of knowing your family will not have a financial burden if something were to happen to you.</p>
    </div>
    <h2 class="also-title">We Also Specialize In:</h2>
    <ul class="also-list">
      <li><svg class="tick"><use href="#tick"/></svg>Medicare Supplement Insurance (Medigap)</li>
      <li><svg class="tick"><use href="#tick"/></svg>Annuities</li>
      <li><svg class="tick"><use href="#tick"/></svg>Mortgage Protection Insurance</li>
    </ul>
    <p class="footnote">*Based on an insured that is a 65 year old, non-smoking female<br>that has no medical conditions with a death benefit of $2k</p>
    <p class="call"><span class="call-label">Call us now:</span><span class="call-number">(208)555.0147</span></p>
    <p class="contact-line contact-email"><svg class="contact-icon"><use href="#mail"/></svg>tkelwer@corvantshield.com</p>
    <p class="contact-line contact-web"><svg class="contact-icon"><use href="#globe"/></svg>corvantshield.com</p>
    <div class="social"><span></span><span></span></div>
  </div>
</article>

<!-- ================= Letter, greyscale ================= -->
<article class="flyer letter mono" style="left:42px;top:624px">
  <div class="sheet">
    <svg class="art" viewBox="0 0 456 587">
      <path role="img" aria-label="Photo of a smiling senior couple embracing at home" class="fill-photo" d="M150,0H456V214C300,200 150,236 0,230V112C70,104 132,62 150,0Z"/>
      <path class="fill-paper" d="M0,0H176C156,64 90,112 0,120Z"/>
      <path class="line-ink" stroke-width="3" d="M0,121C86,112 154,64 176,0"/>
      <path class="line-red" stroke-width="1.5" d="M0,128C94,118 166,66 188,0"/>
      <path class="fill-paper" d="M0,230C150,236 300,204 456,208V260H0Z"/>
      <path class="line-ink" stroke-width="5" d="M0,229C150,237 300,205 456,208"/>
      <path class="line-grey" stroke-width="1.5" d="M0,238C150,244 300,214 456,217"/>
      <path class="line-ink" stroke-width="4" d="M0,523C150,492 300,514 456,496"/>
      <path class="fill-footer" d="M0,530C150,500 300,520 456,503V587H0Z"/>
    </svg>
    <div class="brand"><span class="brand-mark"></span><span class="brand-name">CORVANT SHIELD</span></div>
    <h1 class="headline"><span>Our</span><span class="accent">Plans Are</span><span>Based on Yours</span></h1>
    <section class="benefits">
      <h2 class="benefits-tab">Benefits:</h2>
      <ul class="benefit-list">
        <li><svg class="tick"><use href="#tick"/></svg>All plans we offer are state regulated</li>
        <li><svg class="tick"><use href="#tick"/></svg>Relatively low monthly premiums</li>
        <li><svg class="tick"><use href="#tick"/></svg>Premiums can never increase</li>
        <li><svg class="tick"><use href="#tick"/></svg>Your policy can never be cancelled as long as you pay your premium</li>
        <li><svg class="tick"><use href="#tick"/></svg>No medical exams</li>
        <li><svg class="tick"><use href="#tick"/></svg>Guaranteed Death Benefit</li>
        <li><svg class="tick"><use href="#tick"/></svg>Many policies we offer are Guaranteed Acceptance, "Day 1" coverage, have a child/grandchild rider and/or have an accelerated death benefit rider</li>
      </ul>
    </section>
    <h2 class="section-title">Final Expense Insurance</h2>
    <div class="body-copy justify intro"><p>Final Expense Insurance is a type of permanent whole life insurance insurance where the death benefit is used to cover (but not limited to) medical costs, funeral costs and other end-of-life expenses. It is a budget friendly option with a death benefit of up to $40k.</p></div>
    <dl class="rates">
      <div class="rate"><dt>Monthly premiums as low as</dt><dd>$11*</dd></div>
      <div class="rate"><dt>Death Benefits as high as</dt><dd>$40,000</dd></div>
    </dl>
    <div class="body-copy story">
      <p>Unforeseen events and a lack of the right kind of insurance can spell trouble quickly. Contact us today, to set up a free assessment time. We will analyze your insurance needs and get you and your family the right coverage quickly at a budget friendly price.</p>
      <p>We have been helping clients in Northern Idaho/Eastern Washington prepare for the unknown.</p>
      <p>We have access to the industry's top insurance carriers so you can get the right coverage, that fits your budget.</p>
      <p>Find out how we can give you the peace of mind of knowing your family will not have a financial burden if something were to happen to you.</p>
    </div>
    <h2 class="also-title">We Also Specialize In:</h2>
    <ul class="also-list">
      <li><svg class="tick"><use href="#tick"/></svg>Medicare Supplement Insurance (Medigap)</li>
      <li><svg class="tick"><use href="#tick"/></svg>Annuities</li>
      <li><svg class="tick"><use href="#tick"/></svg>Mortgage Protection Insurance</li>
    </ul>
    <p class="footnote">*Based on an insured that is a 65 year old, non-smoking female<br>that has no medical conditions with a death benefit of $2k</p>
    <p class="call"><span class="call-label">Call us now:</span><span class="call-number">(208)555.0147</span></p>
    <p class="contact-line contact-email"><svg class="contact-icon"><use href="#mail"/></svg>tkelwer@corvantshield.com</p>
    <p class="contact-line contact-web"><svg class="contact-icon"><use href="#globe"/></svg>corvantshield.com</p>
    <div class="social"><span></span><span></span></div>
  </div>
</article>

<!-- ================= Rack, greyscale ================= -->
<article class="flyer rack mono" style="left:476px;top:621px">
  <div class="sheet">
    <svg class="art" viewBox="0 0 252 587">
      <path role="img" aria-label="Photo of a smiling senior couple embracing at home" class="fill-photo" d="M105,0H252V180C170,174 80,196 0,192V68C55,62 95,36 105,0Z"/>
      <path class="line-ink" stroke-width="2.5" d="M0,70C56,63 96,36 108,0"/>
      <path class="line-red" stroke-width="1.2" d="M0,75C62,68 104,38 116,0"/>
      <path class="fill-paper" d="M0,192C80,198 170,176 252,180V215H0Z"/>
      <path class="line-ink" stroke-width="4" d="M0,191C80,198 170,175 252,179"/>
      <path class="line-grey" stroke-width="1.2" d="M0,198C80,205 170,183 252,187"/>
      <path class="line-ink" stroke-width="3.5" d="M0,527C80,505 170,522 252,506"/>
      <path class="fill-footer" d="M0,533C80,511 170,528 252,512V587H0Z"/>
    </svg>
    <div class="brand"><span class="brand-mark"></span><span class="brand-name">CORVANT SHIELD</span></div>
    <h1 class="headline"><span>Our</span><span class="accent">Plans Are</span><span>Based on Yours</span></h1>
    <section class="benefits">
      <h2 class="benefits-tab">Benefits:</h2>
      <ul class="benefit-list">
        <li><svg class="tick"><use href="#tick"/></svg>All plans we offer are state regulated</li>
        <li><svg class="tick"><use href="#tick"/></svg>Relatively low monthly premiums</li>
        <li><svg class="tick"><use href="#tick"/></svg>Premiums can never increase</li>
        <li><svg class="tick"><use href="#tick"/></svg>Your policy can never be cancelled as long as you pay your premium</li>
        <li><svg class="tick"><use href="#tick"/></svg>No medical exams</li>
        <li><svg class="tick"><use href="#tick"/></svg>Guaranteed Death Benefit</li>
        <li><svg class="tick"><use href="#tick"/></svg>Many policies we offer are Guaranteed Acceptance, "Day 1" coverage, have a child/grandchild rider and/or have an accelerated death benefit rider</li>
      </ul>
    </section>
    <h2 class="section-title">Final Expense Insurance</h2>
    <div class="body-copy justify intro"><p>Final Expense Insurance is a type of permanent whole life insurance where the death benefit is used to cover (but not limited to) medical costs, funeral costs and other end-of-life expenses. It is a budget friendly option with a death benefit of up to $40k.</p></div>
    <dl class="rates">
      <div class="rate"><dt>Monthly premiums as low as</dt><dd>$11*</dd></div>
      <div class="rate"><dt>Death Benefits as high as</dt><dd>$40,000</dd></div>
    </dl>
    <div class="body-copy story">
      <p>Unforeseen events and a lack of the right kind of insurance can spell trouble quickly. Contact us today, to set up a free assessment time. We will analyze your insurance needs and get you and your family the right coverage quickly at a budget friendly price.</p>
      <p>We have been helping clients in Northern Idaho/Eastern Washington prepare for the unknown.</p>
      <p>We have access to the industry's top insurance carriers so you can get the right coverage, that fits your budget.</p>
      <p>Find out how we can give you the peace of mind of knowing your family will not have a financial burden if something were to happen to you.</p>
    </div>
    <h2 class="also-title">We Also Specialize In:</h2>
    <ul class="also-list">
      <li><svg class="tick"><use href="#tick"/></svg>Medicare Supplement Insurance (Medigap)</li>
      <li><svg class="tick"><use href="#tick"/></svg>Annuities</li>
      <li><svg class="tick"><use href="#tick"/></svg>Mortgage Protection Insurance</li>
    </ul>
    <p class="footnote">*Based on an insured that is a 65 year old, non-smoking female<br>that has no medical conditions with a death benefit of $2k</p>
    <p class="call"><span class="call-label">Call us now:</span><span class="call-number">(208)555.0147</span></p>
    <p class="contact-line contact-email"><svg class="contact-icon"><use href="#mail"/></svg>tkelwer@corvantshield.com</p>
    <p class="contact-line contact-web"><svg class="contact-icon"><use href="#globe"/></svg>corvantshield.com</p>
    <div class="social"><span></span><span></span></div>
  </div>
</article>

<!-- ================= Postcard, greyscale ================= -->
<article class="flyer postcard mono" style="left:746px;top:718px">
  <div class="sheet">
    <svg class="art" viewBox="0 0 315 467">
      <path role="img" aria-label="Photo of a smiling senior couple embracing at home" class="fill-photo" d="M128,0H315V176C220,168 100,192 0,188V74C62,68 114,42 128,0Z"/>
      <path class="line-ink" stroke-width="2.5" d="M0,76C64,69 116,42 130,0"/>
      <path class="line-red" stroke-width="1.2" d="M0,81C70,74 124,44 138,0"/>
      <path class="fill-paper" d="M0,188C100,194 220,172 315,176V205H0Z"/>
      <path class="line-ink" stroke-width="4" d="M0,187C100,195 220,171 315,175"/>
      <path class="line-grey" stroke-width="1.2" d="M0,194C100,202 220,179 315,183"/>
      <path class="line-ink" stroke-width="3.5" d="M0,412C100,390 220,406 315,392"/>
      <path class="fill-footer" d="M0,418C100,396 220,412 315,398V467H0Z"/>
    </svg>
    <div class="brand"><span class="brand-mark"></span><span class="brand-name">CORVANT SHIELD</span></div>
    <h1 class="headline"><span>Our</span><span class="accent">Plans Are</span><span>Based on Yours</span></h1>
    <section class="benefits">
      <h2 class="benefits-tab">Benefits:</h2>
      <ul class="benefit-list">
        <li><svg class="tick"><use href="#tick"/></svg>All plans we offer are state regulated</li>
        <li><svg class="tick"><use href="#tick"/></svg>Relatively low monthly premiums</li>
        <li><svg class="tick"><use href="#tick"/></svg>Premiums can never increase</li>
        <li><svg class="tick"><use href="#tick"/></svg>Your policy can never be cancelled as long as you pay your premium</li>
        <li><svg class="tick"><use href="#tick"/></svg>No medical exams</li>
        <li><svg class="tick"><use href="#tick"/></svg>Guaranteed Death Benefit</li>
        <li><svg class="tick"><use href="#tick"/></svg>Many policies we offer are Guaranteed Acceptance, "Day 1" coverage, have a child/grandchild rider and/or have an accelerated death benefit rider</li>
      </ul>
    </section>
    <h2 class="section-title">Final Expense Insurance</h2>
    <div class="body-copy justify intro"><p>Final Expense Insurance is a type of permanent whole life insurance where the death benefit is used to cover (but not limited to) medical costs, funeral costs and other end-of-life expenses. It is a budget friendly option with a death benefit of up to $40k.</p></div>
    <dl class="rates">
      <div class="rate"><dt>Monthly premiums as low as</dt><dd>$11*</dd></div>
      <div class="rate"><dt>Death Benefits as high as</dt><dd>$40,000</dd></div>
    </dl>
    <div class="body-copy story">
      <p>Unforeseen events and a lack of the right kind of insurance can spell trouble quickly. Contact us today, to set up a free assessment time. We will analyze your insurance needs and get you and your family the right coverage quickly at a budget friendly price.</p>
      <p>We have been helping clients in Northern Idaho/Eastern Washington prepare for the unknown.</p>
      <p>We have access to the industry's top insurance carriers so you can get the right coverage, that fits your budget.</p>
      <p>Find out how we can give you the peace of mind of knowing your family will not have a financial burden if something were to happen to you.</p>
    </div>
    <h2 class="also-title">We Also Specialize In:</h2>
    <ul class="also-list">
      <li><svg class="tick"><use href="#tick"/></svg>Medicare Supplement Insurance (Medigap)</li>
      <li><svg class="tick"><use href="#tick"/></svg>Annuities</li>
      <li><svg class="tick"><use href="#tick"/></svg>Mortgage Protection Insurance</li>
    </ul>
    <p class="footnote">*Based on an insured that is a 65 year old, non-smoking female<br>that has no medical conditions with a death benefit of $2k</p>
    <p class="call"><span class="call-label">Call us now:</span><span class="call-number">(208)555.0147</span></p>
    <p class="contact-line contact-email"><svg class="contact-icon"><use href="#mail"/></svg>tkelwer@corvantshield.com</p>
    <p class="contact-line contact-web"><svg class="contact-icon"><use href="#globe"/></svg>corvantshield.com</p>
    <div class="social"><span></span><span></span></div>
  </div>
</article>

<p class="size-label" style="left:229px;top:538px">8.5x11</p>
<p class="size-label" style="left:582px;top:538px">3.5x8.5</p>
<p class="size-label" style="left:884px;top:538px">4x6</p>
<p class="size-label" style="left:229px;top:1122px">8.5x11</p>
<p class="size-label" style="left:577px;top:1122px">3.5x8.5</p>
<p class="size-label" style="left:884px;top:1122px">4x6</p>

</body>
</html>
```